Hunting Ethics Organization Needs a Web Design with Logo Refresh

This project involves the creation of a website design including the homepage design, inside page design, and logo refinements. Our organization is Tessaly, and we are a not-for-profit hunting ethics organization.
The focus of the new website design is to bring attention the mission of our organization, provide an overview of the areas where our organization deploys its resources to support the modern hunter, and to encourage visitors to support our organization by donating in support of the organization’s mission.
The winning design will be implemented in Wordpress by our in-house team. If you have questions about how any particular design element may translate to Wordpress, please feel free to post questions in response to this brief. In general, however, we’re more focused on the evolution and delivery of a strong overall design aesthetic – we’ll shoulder the responsibility of how we translate that design into Wordpress.
See attached design brief for full details.

```html
<!DOCTYPE html>
<html lang="en">
<head>
<meta charset="utf-8">
<title>Tessaly – The Hunter's Institute</title>
<link href="https://fonts.googleapis.com/css2?family=Roboto:wght@400;500;700&family=Roboto+Condensed:wght@400;700&display=swap" rel="stylesheet">
<style>
:root{
  --navy:#1c2a8c;
  --navy-deep:#1f2c89;
  --ink:#333;
  --rule:#e3e3e3;
  --white:#fff;
  --olive:#8f8a55;
  --wood-a:#8b5a36;
  --wood-b:#b07a4c;
}
*{box-sizing:border-box;margin:0;padding:0}
html,body{width:710px;height:1200px;overflow:hidden;background:var(--white)}
body{position:relative;font-family:"Roboto",sans-serif;color:var(--ink)}
.abs{position:absolute}

/* header */
.brand{left:60px;top:16px}
.brand-row{display:flex;align-items:center;gap:6px}
.brand-mark{width:22px;height:22px;border-radius:50%;background:var(--olive)}
.brand-name{font-weight:500;font-size:28px;letter-spacing:1px;color:var(--navy);line-height:1}
.brand-sub{font-size:8.5px;color:var(--navy);margin-left:28px;margin-top:1px;letter-spacing:.3px}
.brand-tag{font-size:8px;color:#222;margin-left:26px;margin-top:6px}
.nav{left:267px;top:42px;display:flex;gap:21px;font-size:8.5px;color:#222}
.btn-donate{left:592px;top:34px;width:57px;height:27px;background:var(--navy);color:var(--white);font-weight:700;font-size:9.5px;display:flex;align-items:center;justify-content:center}

/* hero */
.hero{left:0;top:87px;width:710px;height:354px;
  background:
    radial-gradient(ellipse 110px 95px at 215px 105px,#6f6c66 0%,#7e7a72 45%,rgba(126,122,114,0) 100%),
    radial-gradient(ellipse 120px 95px at 225px 270px,#f2a94a 0%,#e99a3a 45%,rgba(233,154,58,0) 100%),
    linear-gradient(100deg,var(--wood-a) 0%,var(--wood-b) 52%,#9a6a42 100%)}
.hero-list{left:390px;top:202px;list-style:none;font-family:"Roboto Condensed",sans-serif;color:var(--white);font-size:17.5px;line-height:21px}
.hero-list li{position:relative;padding-left:17px;margin-bottom:11px}
.hero-list li::before{content:"";position:absolute;left:2px;top:7px;width:5px;height:5px;border-right:1.4px solid var(--white);border-bottom:1.4px solid var(--white);transform:rotate(-45deg)}
.dots{left:329px;top:410px;display:flex;gap:2px}
.dots span{width:9px;height:9px;border-radius:50%;background:#111}
.dots span.on{background:transparent;border:1.5px solid #111}

/* feature cards */
.card{top:454px;width:192px;height:158px;box-shadow:0 8px 10px -6px rgba(0,0,0,.35);overflow:hidden}
.card-1{left:59px;background:
  radial-gradient(ellipse 70px 45px at 140px 70px,#d69a5a 0%,rgba(214,154,90,0) 100%),
  linear-gradient(160deg,#3e2a18 0%,#7a5430 40%,#a6703e 70%,#5a3b22 100%)}
.card-2{left:258px;background:
  radial-gradient(ellipse 120px 50px at 96px 55px,#e8f07a 0%,rgba(232,240,122,0) 100%),
  linear-gradient(180deg,#3f5a12 0%,#8fb43a 45%,#4f8a1e 70%,#3b7512 100%)}
.card-3{left:457px;background:
  radial-gradient(ellipse 60px 70px at 80px 70px,#8a6a58 0%,rgba(138,106,88,0) 100%),
  radial-gradient(ellipse 50px 35px at 160px 75px,#ffffff 0%,rgba(255,255,255,0) 100%),
  linear-gradient(135deg,#3a3d40 0%,#5d6164 55%,#cfd0d0 100%)}
.card-label{position:absolute;left:0;top:64px;height:30px;padding:0 13px;background:rgba(0,0,0,.72);color:var(--white);font-family:"Roboto Condensed",sans-serif;font-weight:700;font-size:12px;display:flex;align-items:center}

.rule{left:59px;width:589px;height:1px;background:var(--rule)}

/* mission */
.section-title{font-family:"Roboto Condensed",sans-serif;font-weight:700;color:var(--navy);font-size:11px}
.mission-title{left:59px;top:672px}
.mission-copy{left:59px;top:698px;width:330px;font-size:8.4px;line-height:17px;color:#333}
.mission-link{left:59px;top:816px;font-size:8px;font-weight:700;color:var(--navy);letter-spacing:.2px}
.mission-photo{left:423px;top:675px;width:225px;height:160px;background:
  radial-gradient(ellipse 60px 40px at 150px 60px,#e3b89c 0%,rgba(227,184,156,0) 100%),
  radial-gradient(ellipse 110px 90px at 110px 85px,#cfdbe6 0%,rgba(207,219,230,0) 100%),
  linear-gradient(110deg,#ffffff 30%,#e6edf4 60%,#a9c1dc 100%)}

/* sponsors */
.sponsor-title{left:0;width:710px;top:883px;text-align:center}
.arrow{top:942px;width:15px;height:15px;border-radius:50%;background:#a8a8a8;display:flex;align-items:center;justify-content:center}
.sponsor{top:928px;height:40px;display:flex;align-items:center;gap:6px;font-weight:700;font-size:14px}
.sponsor .dot{width:10px;height:10px;border-radius:50%}

/* footer */
.footer{left:0;top:1005px;width:710px;height:195px;background:var(--navy-deep)}
.f-title{font-size:8px;font-weight:700;letter-spacing:.2px;color:var(--white)}
.f-text{font-size:8px;color:var(--white)}
.email{left:60px;top:1068px;width:187px;height:29px;background:var(--white);display:flex}
.email-field{flex:1;display:flex;align-items:center;gap:7px;padding-left:9px;font-size:8px;color:#777}
.email-go{width:29px;background:var(--olive);display:flex;align-items:center;justify-content:center}
.contact-line{display:flex;align-items:center;gap:8px;font-size:8px;color:var(--white)}
.social{left:578px;top:1053px;display:flex;gap:7px}
.social span{width:20px;height:20px;border-radius:50%;background:var(--white);display:flex;align-items:center;justify-content:center}
.f-rule{left:60px;top:1124px;width:589px;height:1px;background:rgba(255,255,255,.25)}
.f-links{left:0;width:710px;top:1147px;text-align:center;font-size:7.5px;color:var(--white)}
.f-links span{margin:0 4px}
.copy{left:0;width:710px;top:1165px;text-align:center;font-size:7.5px;color:var(--white)}
</style>
</head>
<body>

<header>
  <div class="abs brand">
    <div class="brand-row"><span class="brand-mark"></span><span class="brand-name">TESSALY</span></div>
    <div class="brand-sub">THE HUNTER'S INSTITUTE</div>
    <div class="brand-tag">Protecting the future of hunting</div>
  </div>
  <nav class="abs nav"><span>About Us</span><span>Hunting Ethics</span><span>Conservation</span><span>Get Involved</span><span>Contact Us</span></nav>
  <div class="abs btn-donate">Donate</div>
</header>

<section>
  <div class="abs hero" role="img" aria-label="Glass jar of coins with an orange donate note on a wooden table"></div>
  <ul class="abs hero-list">
    <li>Protect the heritage of hunting</li>
    <li>Help us protect the future of hunting</li>
    <li>Support us as we empower the<br>modern hunter</li>
  </ul>
  <div class="abs dots"><span></span><span></span><span class="on"></span><span></span><span></span></div>
</section>

<section>
  <div class="abs card card-1" role="img" aria-label="Wild cat resting on a branch"><div class="card-label">HUNTING ETHICS</div></div>
  <div class="abs card card-2" role="img" aria-label="Lone tree on a green field"><div class="card-label">CONSERVATION</div></div>
  <div class="abs card card-3" role="img" aria-label="Volunteer holding a get involved sign"><div class="card-label">GET INVOLVED</div></div>
</section>

<div class="abs rule" style="top:641px"></div>

<section>
  <h2 class="abs section-title mission-title">ORGANIZATION'S MISSION</h2>
  <p class="abs mission-copy">There are many variations of passages of Lorem Ipsum available, but the majority have suffered alteration in some form, by injected humour, or randomised words which don't look even slightly believable. If you are going to use a passage of Lorem Ipsum, you need to be sure there isn't anything embarrassing hidden in the middle of text. All the Lorem Ipsum generators on the Internet tend to repeat predefined chunks as necessary, making this the first true generator on the Internet</p>
  <div class="abs mission-link">JOIN US OR DONATE TODAY</div>
  <div class="abs mission-photo" role="img" aria-label="Hand drawing a network of connected people"></div>
</section>

<div class="abs rule" style="top:858px"></div>

<section>
  <h2 class="abs section-title sponsor-title">OUR SPONSOR</h2>
  <div class="abs arrow" style="left:59px"><svg width="7" height="7" viewBox="0 0 7 7"><path d="M4.8 1 2.2 3.5 4.8 6" fill="none" stroke="#fff" stroke-width="1.5"/></svg></div>
  <div class="abs sponsor" style="left:100px;color:#d6246e"><span class="dot" style="background:#d6246e"></span>Field Sisters</div>
  <div class="abs sponsor" style="left:232px;color:#c8102e">Ridgeline</div>
  <div class="abs sponsor" style="left:352px;color:#1b2c5a"><span class="dot" style="background:#c8102e;border-radius:2px"></span>Trailhead Cap</div>
  <div class="abs sponsor" style="left:517px;color:#111"><span class="dot" style="background:#e39a1c;border-radius:1px"></span>Pinecrest</div>
  <div class="abs arrow" style="left:634px"><svg width="7" height="7" viewBox="0 0 7 7"><path d="M2.2 1 4.8 3.5 2.2 6" fill="none" stroke="#fff" stroke-width="1.5"/></svg></div>
</section>

<footer>
  <div class="abs footer"></div>
  <div class="abs f-title" style="left:60px;top:1031px">NEWSLETTER SUBSCRIBE</div>
  <div class="abs f-text" style="left:60px;top:1046px">Making this the first true generator on the Internet</div>
  <div class="abs email">
    <div class="email-field"><svg width="9" height="7" viewBox="0 0 9 7"><rect x=".5" y=".5" width="8" height="6" fill="none" stroke="#888"/><path d="M.5.5 4.5 4 8.5.5" fill="none" stroke="#888"/></svg>E mail Address</div>
    <div class="email-go"><svg width="13" height="13" viewBox="0 0 13 13"><circle cx="6.5" cy="6.5" r="6.5" fill="#fff"/><path d="M5.3 3.8 8 6.5 5.3 9.2" fill="none" stroke="#8f8a55" stroke-width="1.8"/></svg></div>
  </div>

  <div class="abs f-title" style="left:300px;top:1031px">CONTACT US</div>
  <div class="abs contact-line" style="left:300px;top:1054px">
    <svg width="6" height="8" viewBox="0 0 6 8"><path d="M3 8C1 5 0 4 0 3a3 3 0 0 1 6 0c0 1-1 2-3 5z" fill="#fff"/><circle cx="3" cy="3" r="1" fill="#1f2c89"/></svg>
    <span style="margin-left:3px">418 Alder Grove Road, Millbrook, CT 06420</span>
  </div>
  <div class="abs contact-line" style="left:300px;top:1079px">
    <svg width="8" height="8" viewBox="0 0 8 8"><path d="M1.5 0 3 2 2.2 3.2C2.8 4.4 3.6 5.2 4.8 5.8L6 5 8 6.5 7 8C3.5 8 0 4.5 0 1z" fill="#fff"/></svg>
    <span style="margin-left:3px">555-014-2290</span><span style="margin:0 6px">|</span>
    <svg width="9" height="7" viewBox="0 0 9 7"><rect width="9" height="7" fill="#fff"/><path d="M0 0 4.5 3.8 9 0" fill="none" stroke="#1f2c89"/></svg>
    <span style="margin-left:3px">hello@tessaly-institute.org</span>
  </div>

  <div class="abs f-title" style="left:588px;top:1031px">FOLLOW US ON</div>
  <div class="abs social">
    <span aria-label="Community chat"><svg width="10" height="9" viewBox="0 0 10 9"><path d="M1 0h8a1 1 0 0 1 1 1v5a1 1 0 0 1-1 1H4L1.5 9V7H1a1 1 0 0 1-1-1V1a1 1 0 0 1 1-1z" fill="#1f2c89"/></svg></span>
    <span aria-label="Share"><svg width="10" height="10" viewBox="0 0 10 10"><circle cx="8" cy="2" r="1.7" fill="#1f2c89"/><circle cx="2" cy="5" r="1.7" fill="#1f2c89"/><circle cx="8" cy="8" r="1.7" fill="#1f2c89"/><path d="M8 2 2 5 8 8" fill="none" stroke="#1f2c89" stroke-width="1"/></svg></span>
    <span aria-label="Newsletter"><svg width="10" height="8" viewBox="0 0 10 8"><rect width="10" height="8" rx="1" fill="#1f2c89"/><path d="M.5.5 5 4.5 9.5.5" fill="none" stroke="#fff" stroke-width="1"/></svg></span>
  </div>

  <div class="abs f-rule"></div>
  <div class="abs f-links"><span>About Us</span>|<span>Hunting Ethics</span>|<span>Conservation</span>|<span>Get Involved</span>|<span>Contact Us</span>|<span>Donate</span></div>
  <div class="abs copy">Copyrights @ 2015 All Rights Reserved</div>
</footer>

</body>
</html>
```